New site for parent-to-parent advice in spanish requieres Wordpress design

Nidoluz.com ("time for child" in spanish) is a web site dedicated to give support from father to father in order to attend small babies and childs. The core idea is that divorced, single or widow male parents can get advice from other parents on attending our kids alone, as for short term visits or as single parents. It must be fun and easy to navigate, simple, practical and male-oriented. The site will be in spanish and Mexico and Latin-america market. Some subcategories will be ages of kids (toddlers, kids, preadolescents, adolescents; Bebés, Niños, Preadolescentes, Adolescentes) and other will be the father situation (widows, singles, divorced or even married; Viudos, Solteros, Divorciados, Casados).
Updates

Project Deadline Extended
Reason: As some of your questions are if it includes Wordpress Code and the answer is yes, we are recibed request to extend the deadline to workdays in order to can get the code over an unpdated designs. Thanks.

Target Market(s)

Divorced, single or widow male parents can get advice from other parents on attending our kids alone, as for short term visits or as single parents. The site will be in spanish an Latin-America oriented.

Industry/Entity Type

It Support

Requirements
Must have
• Nidoluz.com as the name of the site.
Space for banners well identified, in order to sell publicity but to clearly states wich is advice from the team and what paid publicity.
Nice to have
• Penguins will be prefered as the site mascot or graphic elements, since Penguins are the only animal in which male parent keep in charge of the small ones alone for six months a year -view photo for reference, not necesarly for direct use-
Trinos and Redvecina buttons.

```html
<!DOCTYPE html>
<html lang="es">
<head>
<meta charset="utf-8">
<title>Nidoluz.com — Contactos</title>
<link rel="stylesheet" href="https://fonts.googleapis.com/css2?family=Bebas+Neue&family=Chewy&family=Open+Sans:wght@400;600;700&family=Noto+Serif:ital@1&family=Roboto+Condensed:wght@400;700&display=swap">
<style>
:root{
  --sky-top:#9fd4ee;
  --sky-bottom:#7cc2e6;
  --nav:#2f7f9f;
  --nav-dark:#256a86;
  --nav-active:#2a3036;
  --cream:#fcf3df;
  --ink:#1d2329;
  --side:#57a5c7;
  --side-head:#2f84a8;
  --tips-head:#dfe7ec;
  --tips-body:#5f7789;
  --footer:#222b33;
  --ad-blue:#3b5a9a;
  --ad-bg:#eef1f7;
  --ad-green:#5aa83a;
  --white:#ffffff;
}
*{box-sizing:border-box;margin:0;padding:0}
html,body{width:1005px;height:1200px;overflow:hidden}
body{background:var(--cream);font-family:"Open Sans",Arial,sans-serif;color:var(--ink);font-size:12px}
.wrap{width:591px;margin:0 auto;position:relative}
ul{list-style:none}

/* header */
.site-header{height:104px;background:linear-gradient(var(--sky-top),var(--sky-bottom))}
.site-header .wrap{height:104px}
.brand{position:absolute;left:0;top:4px;display:flex;align-items:center;gap:8px;height:96px;width:200px}
.mascot{width:44px;height:88px;border-radius:22px 22px 8px 8px;background:linear-gradient(#2b3f55,#5f7f9c);flex:none}
.brand-name{font-family:"Bebas Neue",sans-serif;font-size:32px;line-height:32px;color:#1f4f7c;letter-spacing:.5px;white-space:nowrap}
.tagline{position:absolute;left:224px;top:35px;font-family:"Bebas Neue",sans-serif;font-size:18px;line-height:18px;color:var(--white);letter-spacing:.5px;white-space:nowrap}
.social{position:absolute;right:2px;top:32px;display:flex;gap:2px}
.social a{width:41px;height:41px;display:flex;align-items:flex-end;justify-content:center;padding-bottom:4px;font-size:7px;color:var(--white);text-decoration:none;font-weight:600}
.social .s1{background:#2f5b9c}
.social .s2{background:#3ab0e6}

/* nav */
.nav{height:29px;background:repeating-linear-gradient(90deg,var(--nav) 0 3px,var(--nav-dark) 3px 4px)}
.nav ul{display:flex;height:29px;justify-content:space-between;margin-left:-6px;margin-right:-16px}
.nav li{font-family:"Bebas Neue",sans-serif;font-size:14px;color:var(--white);line-height:29px;padding:0 5px;position:relative;white-space:nowrap}
.nav li+li::before{content:"";position:absolute;left:-3px;top:13px;width:4px;height:4px;border-radius:50%;background:var(--white)}
.nav li.active{background:var(--nav-active);padding:0 13px}

/* tips */
.tips{margin-top:8px;height:72px;border:1px solid #9fb0bb}
.tips-head{height:20px;background:var(--tips-head);position:relative}
.tips-head h2{font-family:"Bebas Neue",sans-serif;font-size:28px;line-height:30px;position:absolute;left:6px;top:-6px;color:var(--ink);font-weight:400}
.arrows{position:absolute;right:6px;top:2px;display:flex;gap:1px}
.arrows span{width:15px;height:16px;background:var(--white);border:1px solid #b8c4cc;display:flex;align-items:center;justify-content:center}
.tips-body{height:50px;background:var(--tips-body);color:var(--white);font-family:"Noto Serif",serif;font-style:italic;font-size:10px;line-height:16px;text-align:center;padding:4px 14px 0;position:relative}
.quote{position:absolute;right:8px;bottom:-10px;font-size:34px;color:#8ea3b3;font-style:normal}

/* columns */
.columns{display:flex;gap:15px;margin-top:16px;height:704px}
.main{width:389px}
.sidebar{width:187px}

.ad-bar{height:56px;border:1px solid #c7cfdc;background:var(--ad-bg)}
.ad-bar .bar{height:23px;background:var(--ad-blue);color:var(--white);font-weight:700;font-size:13px;padding-left:6px;line-height:23px}
.ad-bar .row{display:flex;align-items:center;height:31px;padding:0 6px;gap:7px;font-size:11.5px;white-space:nowrap}
.ad-bar .row b{font-weight:700}
.ad-bar .row span{color:#3b5a9a}
.ad-bar .btn{margin-left:auto;background:var(--ad-green);color:var(--white);font-size:9px;font-weight:700;font-style:normal;padding:3px 8px}

.section-title{font-family:"Bebas Neue",sans-serif;font-size:22px;line-height:22px;font-weight:400;margin-top:23px}
.map{height:224px;background:linear-gradient(135deg,#e8e4dc,#d9d6cf);border:1px solid #c8c4bb}
.address{margin-top:18px;font-size:11.5px;line-height:15px}
.section-title.msg{margin-top:31px}
.form label{display:block;font-weight:700;font-size:12px;line-height:16px;margin-top:4px}
.form .field{width:95px;height:13px;background:var(--white);border:1px solid #c9c9c9;margin-top:3px}
.form .area{width:100%;height:64px;background:var(--white);border:1px solid #c9c9c9;margin-top:3px}
.send{display:block;margin:16px 0 0 auto;width:78px;height:28px;background:var(--side-head);color:var(--white);font-family:"Chewy",cursive;font-size:18px;text-align:center;line-height:28px}
.ad-bar.bottom{margin-top:14px}

/* sidebar */
.side-block{background:var(--side)}
.side-block h3{font-family:"Chewy",cursive;font-weight:400;font-size:21px;color:var(--white);background:var(--side-head);height:36px;line-height:36px;padding-left:11px;white-space:nowrap}
.side-block ul{padding:4px 0 4px 34px}
.side-block li{color:var(--white);font-size:11.5px;line-height:19px;list-style:disc}
.side-ad{margin-top:4px;height:158px;background:var(--white);border:1px solid #bbb;padding:6px 5px;text-align:center;font-family:"Roboto Condensed",sans-serif}
.side-ad .t1{color:#1a6ab0;font-size:18px;line-height:20px;white-space:nowrap;letter-spacing:-.3px}
.side-ad .t2{color:#d2232a;font-size:8px;line-height:9px;font-weight:700}
.side-ad .t3{color:#1a6ab0;font-size:13px;line-height:15px;margin-top:8px}
.side-ad .pic-row{display:flex;gap:6px;margin-top:6px;align-items:center}
.side-ad .pic{width:76px;height:48px;background:linear-gradient(#b58a52,#6d4a2c)}
.side-ad .go{background:#f28a2a;color:var(--white);font-size:10px;font-weight:700;padding:5px 8px;white-space:nowrap}

/* footer */
.footer-nav{margin-top:16px;height:30px;background:repeating-linear-gradient(90deg,var(--nav) 0 3px,var(--nav-dark) 3px 4px)}
.footer-nav ul{display:flex;justify-content:space-between;height:30px;margin-left:-4px}
.footer-nav li{font-family:"Bebas Neue",sans-serif;font-size:14px;color:var(--white);line-height:30px;padding:0 4px;position:relative;white-space:nowrap}
.footer-nav li+li::before{content:"";position:absolute;left:-3px;top:13px;width:4px;height:4px;border-radius:50%;background:var(--white)}
.site-footer{background:var(--footer);height:221px;color:var(--white)}
.site-footer .wrap{height:221px}
.fcol{position:absolute;top:14px;width:140px}
.fcol h4{font-family:"Bebas Neue",sans-serif;font-weight:400;font-size:12px;letter-spacing:.3px;margin-bottom:4px}
.fcol ul{padding-left:14px;margin-bottom:9px}
.fcol li{font-size:7.5px;line-height:11px;list-style:disc}
.c1{left:0}.c2{left:150px}.c3{left:301px}
.fsocial{display:flex;gap:4px;margin-top:6px}
.fsocial span{width:40px;height:40px;display:flex;align-items:flex-end;justify-content:center;font-size:6px;padding-bottom:3px;font-weight:600}
.fbrand{position:absolute;left:404px;top:18px;display:flex;align-items:center;gap:6px}
.fbrand .mascot{width:40px;height:84px}
.fbrand .brand-name{color:#5cb6e4;font-size:30px}
.legal{position:absolute;left:0;right:0;top:186px;text-align:center;font-size:7.5px;line-height:11px}
.legal span{margin:0 7px}
</style>
</head>
<body>
<header class="site-header">
  <div class="wrap">
    <div class="brand">
      <div class="mascot" role="img" aria-label="Ilustración de pingüino padre con su cría"></div>
      <span class="brand-name">Nidoluz.com</span>
    </div>
    <p class="tagline">Lorem ipsum dolor sit amet,<br>consectetur adipiscing elit. Phasellus</p>
    <div class="social">
      <a class="s1" href="#">Redvecina</a>
      <a class="s2" href="#">Trinos</a>
    </div>
  </div>
</header>

<nav class="nav">
  <div class="wrap">
    <ul>
      <li>Inicio</li><li>Primeros Pasos</li><li>Padre a Padre</li><li>Hijos por Edades</li><li>Situacion del Padre</li><li>Nosotros</li><li class="active">Contactos</li>
    </ul>
  </div>
</nav>

<div class="wrap">
  <section class="tips">
    <div class="tips-head">
      <h2>Tips!</h2>
      <div class="arrows">
        <span><svg width="6" height="8"><path d="M5 0 L1 4 L5 8Z" fill="#333"/></svg></span>
        <span><svg width="6" height="8"><path d="M1 0 L5 4 L1 8Z" fill="#333"/></svg></span>
      </div>
    </div>
    <div class="tips-body">
      Lorem ipsum dolor sit amet, consectetur adipiscing elit. Vivamus nec sodales ligula. Aenean tincidunt vitae ante eget faucibus. Vivamus ac diam diam. Sed ac sapien cursus diam sagittis consequat sit amet sit amet lectus.
      <span class="quote">”</span>
    </div>
  </section>

  <div class="columns">
    <main class="main">
      <div class="ad-bar">
        <div class="bar">Redvecina</div>
        <div class="row"><b>Create a Redvecina profile</b><span>Sign up for free today!</span><em class="btn">Sign Up</em></div>
      </div>

      <h1 class="section-title">Contactos</h1>
      <div class="map" role="img" aria-label="Mapa de ubicación de la oficina"></div>
      <p class="address">Dirección: Av. Los Pinos N°48 (Centro)<br>Telf.: 591-4-5550182 • 591-4-555027 • 591-4-5550394<br>Email: info@nidoluz.com</p>

      <h2 class="section-title msg">Envienos un mensaje</h2>
      <div class="form">
        <label>Nombre:</label><div class="field"></div>
        <label>Email:</label><div class="field"></div>
        <label>Mensaje:</label><div class="area"></div>
        <span class="send">Enviar</span>
      </div>

      <div class="ad-bar bottom">
        <div class="bar">Redvecina</div>
        <div class="row"><b>Create a Redvecina profile</b><span>Sign up for free today!</span><em class="btn">Sign Up</em></div>
      </div>
    </main>

    <aside class="sidebar">
      <div class="side-block">
        <h3>Primeros Pasos</h3>
        <ul><li>Lorem Ipsum</li><li>Dolor sit amet</li><li>Consectetur</li><li>Adipiscing elit</li></ul>
        <h3>Padre a Padre</h3>
        <ul><li>Lorem Ipsum</li><li>Dolor sit amet</li><li>Consectetur</li><li>Adipiscing elit</li></ul>
        <h3>Hijos por Edades</h3>
        <ul><li>Bebés</li><li>Niños</li><li>Preadolescentes</li><li>Adolescentes</li></ul>
        <h3>Situacion del Padre</h3>
        <ul><li>Viudos</li><li>Solteros</li><li>Divorciados</li><li>Casados</li></ul>
        <h3>Tips</h3>
      </div>
      <div class="side-ad">
        <div class="t1">Apartamentos Temporales</div>
        <div class="t2">EL MEJOR PRECIO EN LOS<br>MEJORES APARTAMENTOS</div>
        <div class="t3">LAS MEJORES OFERTAS EN<br>TEMPORADA ALTA</div>
        <div class="pic-row">
          <div class="pic" role="img" aria-label="Foto de interior de apartamento"></div>
          <span class="go">INFORMESE YA</span>
        </div>
      </div>
    </aside>
  </div>
</div>

<nav class="footer-nav">
  <div class="wrap">
    <ul><li>Inicio</li><li>Primeros Pasos</li><li>Padre a Padre</li><li>Hijos por Edades</li><li>Situacion del Padre</li><li>Nosotros</li><li>Contactos</li></ul>
  </div>
</nav>

<footer class="site-footer">
  <div class="wrap">
    <div class="fcol c1">
      <h4>Inicio</h4>
      <h4>Primeros Pasos</h4>
      <ul><li>Lorem Ipsum</li><li>Dolor sit amet</li><li>Consectetur</li><li>Adipiscing elit</li></ul>
      <h4>Padre a Padre</h4>
      <ul><li>Lorem Ipsum</li><li>Dolor sit amet</li><li>Consectetur</li><li>Adipiscing elit</li></ul>
    </div>
    <div class="fcol c2">
      <h4>Hijos por Edades</h4>
      <ul><li>Bebés</li><li>Niños</li><li>Preadolescentes</li><li>Adolescentes</li></ul>
      <h4>Situacion del Padre</h4>
      <ul><li>Viudos</li><li>Solteros</li><li>Divorciados</li><li>Casados</li></ul>
    </div>
    <div class="fcol c3">
      <h4>Nosotros</h4>
      <h4>Contactos</h4>
      <div class="fsocial">
        <span style="background:#2f5b9c">Redvecina</span>
        <span style="background:#3ab0e6">Trinos</span>
      </div>
    </div>
    <div class="fbrand">
      <div class="mascot" role="img" aria-label="Ilustración de pingüino padre con su cría"></div>
      <span class="brand-name">Nidoluz.com</span>
    </div>
    <p class="legal"><span>Terms and Conditions</span><span>Privacy Policy</span><span>How It Works</span><span>Acceptable Use Policy</span><br>© 2013 Nidoluz.com. All rights reserved.</p>
  </div>
</footer>
</body>
</html>
```